Real Estate Website

I am looking for a website design for a website that will be featuring real estate listings across Australia. It will be a website for a real estate agency that operates through all states in Australia.

We like the designs of https://www.brightnest.com.au/ and https://valtoria.example/

On the brightnest website, we like the sell, buy, sold tabs but would also like lease, and agents. We also need a button somewhere for 'Join Agent Pivola' and 'Login'

On the Valtoria site it has a concierge section and we want something like that on the home page.

The contact details to show in the footer are:

Shop 2217B
Level 1 Harbourgate Shopping Centre
87 Quillon Terrace
Southport

Attached are various versions of the logo and some intro text to go on the home page.

```html
<!DOCTYPE html>
<html lang="en">
<head>
<meta charset="utf-8">
<title>Agent Pivola – Australia's Premier Real Estate Network</title>
<link href="https://fonts.googleapis.com/css2?family=Poppins:wght@400;500;600;700&family=Dancing+Script:wght@700&display=swap" rel="stylesheet">
<style>
:root{
  --gold-light:#d8c16a;
  --gold:#a88a3c;
  --gold-dark:#6e5220;
  --brown:#8a6a2c;
  --ink:#1b1b1b;
  --muted:#555;
  --line:#d9d9d9;
  --white:#fff;
  --gold-grad:linear-gradient(135deg,#d6bf68 0%,#a6873a 50%,#6f5421 100%);
}
*{box-sizing:border-box;margin:0;padding:0}
html,body{width:1200px;height:4666px;overflow:hidden}
body{font-family:"Poppins",sans-serif;color:var(--ink);background:var(--white);position:relative}
.abs{position:absolute}
section,header,footer{position:absolute;left:0;width:1200px}
a{color:inherit;text-decoration:none}
.btn{display:flex;align-items:center;justify-content:center;font-weight:600;font-size:13px;text-transform:uppercase;white-space:nowrap}
.btn-gold{background:var(--gold-grad);color:var(--white);border-radius:3px}
.btn-outline{border:2px solid var(--white);color:var(--white);border-radius:4px}

/* header */
.site-header{top:0;height:85px;background:var(--white);z-index:5}
.brand{left:57px;top:0;width:213px;height:145px;background:var(--white);border-radius:0 0 22px 22px;display:flex;align-items:flex-end;justify-content:center;padding-bottom:14px;font-size:20px;font-weight:500;letter-spacing:4px;color:var(--ink)}
.main-nav{left:290px;top:33px;display:flex;gap:29px;font-size:12.5px;font-weight:500;color:#333}
.main-nav .active{color:var(--gold);position:relative}
.main-nav .active::before{content:"";position:absolute;left:0;right:0;top:-30px;height:4px;background:var(--gold)}
.join{left:795px;top:20px;width:201px;height:44px}
.login{left:1008px;top:18px;width:112px;height:48px;border:2px solid var(--ink);border-radius:4px;color:var(--ink)}

/* hero */
.hero{top:85px;height:556px;background:linear-gradient(180deg,#4d6a8a 0%,#2a3a52 40%,#1d2735 62%,#5b4b30 100%)}
.hero-title{left:0;width:1200px;top:130px;text-align:center;font-family:"Dancing Script",cursive;font-size:52px;color:var(--white)}
.hero-sub{left:0;width:1200px;top:217px;text-align:center;font-size:19px;font-weight:500;color:var(--white)}
.tab{top:275px;height:42px}
.search-bar{position:absolute;left:275px;top:349px;width:647px;height:46px;background:var(--white);border-radius:3px;display:flex;align-items:center;overflow:hidden}
.search-bar span{flex:1;padding-left:15px;font-size:12px;color:#444;white-space:nowrap}
.search-bar .btn{width:261px;flex:none;height:100%;border-radius:0;font-size:12.5px}

/* categories */
.cat{top:724px;width:246px;height:208px;border:2px solid var(--gold-light);display:flex;flex-direction:column;align-items:center;justify-content:center;gap:18px;font-size:20px;font-weight:500;background:var(--white)}
.cat.featured{background:var(--gold-grad);color:var(--white);border:none}

/* listings */
.section-title{left:0;width:1200px;text-align:center;font-weight:700;font-size:36px;text-transform:uppercase}
.section-lead{left:0;width:1200px;text-align:center;font-size:14px;color:#333}
.listing{top:1110px;width:288px;height:358px;background:var(--white);box-shadow:0 2px 10px rgba(0,0,0,.15);border-radius:4px;overflow:hidden}
.listing .photo{height:190px}
.listing .name{position:absolute;left:18px;top:210px;font-size:18px;font-weight:500}
.listing .loc{position:absolute;left:18px;top:245px;display:flex;align-items:center;gap:8px;font-size:13.5px;color:#333}
.listing .price{position:absolute;right:14px;top:242px;font-size:19px;font-weight:600;color:var(--brown)}
.listing .specs{position:absolute;left:0;right:0;top:290px;display:flex;justify-content:space-between;padding:0 14px 0 20px;font-size:13px;color:#333}
.listing .spec{display:flex;flex-direction:column;align-items:center;gap:4px}
.arrow{top:1270px;width:36px;height:36px;border:2px solid #222;border-radius:50%;display:flex;align-items:center;justify-content:center}
.arrow.next{border-color:var(--gold)}

/* concierge */
.concierge{top:1562px;height:543px;background:linear-gradient(135deg,#5f7a3a,#3f5a2c 40%,#7a8c55 70%,#4c5f33)}
.concierge-panel{left:145px;top:92px;width:907px;height:353px;background:rgba(150,110,40,.85);border:1px solid rgba(255,255,255,.35);border-radius:6px;color:var(--white);text-align:center}
.concierge-panel h2{margin-top:58px;font-size:36px;font-weight:700}
.concierge-panel p{width:650px;margin:18px auto 0;font-size:14px;line-height:26px}
.concierge-panel .btn{width:181px;height:46px;margin:30px auto 0}

/* gallery */
.tile{overflow:hidden}
.tile-gold{background:linear-gradient(135deg,#a88a3c,#6e5220)}
.tile-gold .inner{position:absolute;left:14px;top:14px;right:14px;bottom:14px;background:var(--gold-grad);display:flex;flex-direction:column;align-items:center;justify-content:center;gap:14px;text-align:center;font-size:17px;line-height:34px;font-weight:500;color:#3a2a0c;padding:0 30px}
.view-more{left:514px;top:2938px;width:170px;height:45px}

/* location */
.location{top:3066px;height:565px;background:linear-gradient(90deg,#dcdcd4 0%,#cfcfc4 30%,#8a6a2c 52%,#8a6a2c 100%)}
.location h2{position:absolute;left:632px;top:103px;font-size:36px;font-weight:600;color:var(--white);text-transform:uppercase}
.loc-search{left:641px;top:187px;width:381px;height:44px;background:var(--white);border-radius:4px;display:flex;align-items:center;justify-content:space-between;padding-left:14px;font-size:16px;color:#333}
.loc-search .go{width:66px;height:38px;margin-right:3px;background:var(--gold-grad);border-radius:4px;display:flex;align-items:center;justify-content:center}
.loc-list{left:645px;top:265px;display:grid;grid-template-columns:197px 197px;row-gap:24px;font-size:17px;color:var(--white)}
.loc-list li{list-style:none;display:flex;align-items:center;gap:12px}

/* contact */
.contact-bg{top:3980px;height:686px;background:linear-gradient(180deg,#7d8a83 0%,#4b4a3e 40%,#4b3a1e 100%)}
.contact-card{left:113px;top:3779px;width:976px;height:471px;background:var(--white);box-shadow:0 2px 12px rgba(0,0,0,.12)}
.contact-card h3{position:absolute;left:28px;top:28px;font-size:22px;font-weight:500}
.field{position:absolute;font-size:13px;color:#222;border-bottom:1px solid var(--line);height:40px}
.submit{left:32px;top:379px;width:170px;height:45px}
.address{left:625px;top:11px;width:347px;height:450px;background:linear-gradient(180deg,#8a6a2c,#7a5c24);border-radius:4px;color:var(--white)}
.address h3{left:32px;top:24px;font-size:22px;font-weight:500;color:var(--white)}
.addr-row{position:absolute;left:24px;display:flex;gap:20px;font-size:13px;line-height:25px}
.addr-row .ico{width:56px;height:56px;border:2px solid rgba(255,255,255,.8);border-radius:50%;display:flex;align-items:center;justify-content:center;flex:none}

/* footer */
.footer-name{left:0;width:1200px;top:4470px;text-align:center;font-size:22px;font-weight:400;letter-spacing:6px;color:var(--gold-light)}
.footer-nav{left:0;width:1200px;top:4528px;display:flex;justify-content:center;gap:30px;font-size:17px;color:var(--white)}
.footer-rule{left:111px;top:4588px;width:977px;height:1px;background:rgba(255,255,255,.6)}
.copy{left:0;width:1200px;top:4612px;text-align:center;font-size:13px;color:var(--white)}
</style>
</head>
<body>

<header class="site-header">
  <div class="abs brand">AGENT PIVOLA</div>
  <nav class="abs main-nav">
    <a class="active">HOME</a><a>BUY</a><a>SELL</a><a>SOLD</a><a>LEASE</a><a>AGENTS</a><a>CONCIERGE</a>
  </nav>
  <a class="abs btn btn-gold join">Join Agent Pivola</a>
  <a class="abs btn login">Login</a>
</header>

<section class="hero" role="img" aria-label="City skyline at dusk reflected on a calm river">
  <h1 class="abs hero-title">Australia's Premier Real Estate Network</h1>
  <p class="abs hero-sub">Connecting Buyers, Sellers &amp; Agents Across Every State</p>
  <a class="abs btn btn-gold tab" style="left:452px;width:61px">Sell</a>
  <a class="abs btn btn-outline tab" style="left:554px;width:88px">Buy</a>
  <a class="abs btn btn-outline tab" style="left:657px;width:88px">Sold</a>
  <div class="search-bar"><span>Start Typing To Find Your Address...</span><a class="btn btn-gold">What's My Property Worth</a></div>
</section>

<section style="top:0;height:0">
  <div class="abs cat" style="left:158px">
    <svg width="70" height="60" viewBox="0 0 70 60" fill="none" stroke="#222" stroke-width="2.5"><path d="M6 30 L28 10 L50 30"/><path d="M12 26 V54 H44 V26"/><rect x="23" y="38" width="10" height="16"/><rect x="40" y="28" width="26" height="14" rx="2" fill="#fff"/></svg>
    Recently Sold
  </div>
  <div class="abs cat featured" style="left:476px">
    <svg width="70" height="60" viewBox="0 0 70 60" fill="none" stroke="#fff" stroke-width="2.5"><rect x="10" y="6" width="50" height="48"/><path d="M22 30 L35 20 L48 30 V48 H22 Z"/><rect x="24" y="38" width="22" height="8"/></svg>
    For Sale
  </div>
  <div class="abs cat" style="left:791px">
    <svg width="70" height="60" viewBox="0 0 70 60" fill="none" stroke="#222" stroke-width="2.5"><path d="M6 28 L30 8 L54 28"/><path d="M12 24 V54 H48 V24"/><rect x="20" y="30" width="20" height="10"/><rect x="36" y="40" width="30" height="14" rx="2" fill="#fff"/></svg>
    For Rent
  </div>

  <h2 class="abs section-title" style="top:1010px">Home For Sale</h2>
  <p class="abs section-lead" style="top:1072px">Lorem Ipsum is simply dummy text of the printing and typesetting industry.</p>

  <div class="abs arrow" style="left:46px"><svg width="14" height="14" viewBox="0 0 14 14" fill="none" stroke="#222" stroke-width="2"><path d="M9 2 L4 7 L9 12"/></svg></div>
  <div class="abs arrow next" style="left:1113px"><svg width="14" height="14" viewBox="0 0 14 14" fill="none" stroke="#8a6a2c" stroke-width="2"><path d="M5 2 L10 7 L5 12"/></svg></div>

  <article class="abs listing" style="left:148px">
    <div class="photo" role="img" aria-label="Modern white single-storey home with dark roof" style="background:linear-gradient(180deg,#d6dde2,#8a8c86 60%,#4f6b36)"></div>
    <div class="name">Agent Pivola</div>
    <div class="loc"><svg width="16" height="18" viewBox="0 0 16 18" fill="none" stroke="#333" stroke-width="1.5"><path d="M8 17 C3 11 2 9 2 7 A6 6 0 0 1 14 7 C14 9 13 11 8 17Z"/><circle cx="8" cy="7" r="2"/></svg>Lorem Ipsum</div>
    <div class="price">$850,000</div>
    <div class="specs">
      <div class="spec"><svg width="22" height="18" viewBox="0 0 22 18" fill="none" stroke="#8a6a2c" stroke-width="1.5"><rect x="2" y="2" width="18" height="8"/><path d="M2 10 V16 M20 10 V16 M2 13 H20"/></svg>3 Beds</div>
      <div class="spec"><svg width="22" height="18" viewBox="0 0 22 18" fill="none" stroke="#8a6a2c" stroke-width="1.5"><path d="M3 9 H19 V12 A4 4 0 0 1 15 16 H7 A4 4 0 0 1 3 12 Z M6 9 V3 H9"/></svg>2 Baths</div>
      <div class="spec"><svg width="22" height="18" viewBox="0 0 22 18" fill="none" stroke="#8a6a2c" stroke-width="1.5"><rect x="3" y="2" width="16" height="14"/><path d="M3 2 L19 16 M11 2 V9 H19"/></svg>1,200 Sqft</div>
    </div>
  </article>
  <article class="abs listing" style="left:454px">
    <div class="photo" role="img" aria-label="Blue two-storey family home with garage" style="background:linear-gradient(180deg,#9cc4e6,#4f6e8c 55%,#5d8a3a)"></div>
    <div class="name">Agent Pivola</div>
    <div class="loc"><svg width="16" height="18" viewBox="0 0 16 18" fill="none" stroke="#333" stroke-width="1.5"><path d="M8 17 C3 11 2 9 2 7 A6 6 0 0 1 14 7 C14 9 13 11 8 17Z"/><circle cx="8" cy="7" r="2"/></svg>Lorem Ipsum</div>
    <div class="price">$850,000</div>
    <div class="specs">
      <div class="spec"><svg width="22" height="18" viewBox="0 0 22 18" fill="none" stroke="#8a6a2c" stroke-width="1.5"><rect x="2" y="2" width="18" height="8"/><path d="M2 10 V16 M20 10 V16 M2 13 H20"/></svg>3 Beds</div>
      <div class="spec"><svg width="22" height="18" viewBox="0 0 22 18" fill="none" stroke="#8a6a2c" stroke-width="1.5"><path d="M3 9 H19 V12 A4 4 0 0 1 15 16 H7 A4 4 0 0 1 3 12 Z M6 9 V3 H9"/></svg>2 Baths</div>
      <div class="spec"><svg width="22" height="18" viewBox="0 0 22 18" fill="none" stroke="#8a6a2c" stroke-width="1.5"><rect x="3" y="2" width="16" height="14"/><path d="M3 2 L19 16 M11 2 V9 H19"/></svg>1,200 Sqft</div>
    </div>
  </article>
  <article class="abs listing" style="left:760px">
    <div class="photo" role="img" aria-label="White two-storey home with dark gables" style="background:linear-gradient(180deg,#c9d6e2,#b7b4ac 55%,#6d7f4a)"></div>
    <div class="name">Agent Pivola</div>
    <div class="loc"><svg width="16" height="18" viewBox="0 0 16 18" fill="none" stroke="#333" stroke-width="1.5"><path d="M8 17 C3 11 2 9 2 7 A6 6 0 0 1 14 7 C14 9 13 11 8 17Z"/><circle cx="8" cy="7" r="2"/></svg>Lorem Ipsum</div>
    <div class="price">$850,000</div>
    <div class="specs">
      <div class="spec"><svg width="22" height="18" viewBox="0 0 22 18" fill="none" stroke="#8a6a2c" stroke-width="1.5"><rect x="2" y="2" width="18" height="8"/><path d="M2 10 V16 M20 10 V16 M2 13 H20"/></svg>3 Beds</div>
      <div class="spec"><svg width="22" height="18" viewBox="0 0 22 18" fill="none" stroke="#8a6a2c" stroke-width="1.5"><path d="M3 9 H19 V12 A4 4 0 0 1 15 16 H7 A4 4 0 0 1 3 12 Z M6 9 V3 H9"/></svg>2 Baths</div>
      <div class="spec"><svg width="22" height="18" viewBox="0 0 22 18" fill="none" stroke="#8a6a2c" stroke-width="1.5"><rect x="3" y="2" width="16" height="14"/><path d="M3 2 L19 16 M11 2 V9 H19"/></svg>1,200 Sqft</div>
    </div>
  </article>
</section>

<section class="concierge" role="img" aria-label="Aerial view of a leafy suburban neighbourhood">
  <div class="abs concierge-panel">
    <h2>AGENT PIVOLA CONCIERGE</h2>
    <p>Lorem Ipsum is simply dummy text of the printing and typesetting industry. Lorem Ipsum has been the industry's standard dummy text ever since the 1500s, when an unknown printer took a galley of type and scrambled it to make a type specimen book.</p>
    <a class="btn btn-outline">Find Out More</a>
  </div>
</section>

<section style="top:0;height:0">
  <h2 class="abs section-title" style="top:2190px">Our Gallery</h2>
  <div class="abs tile" role="img" aria-label="White weatherboard home with gabled roofs" style="left:111px;top:2273px;width:649px;height:286px;background:linear-gradient(180deg,#dfe6ec,#c8c2b4 55%,#5e5a4c)"></div>
  <div class="abs tile" role="img" aria-label="Contemporary two-storey home at dusk" style="left:782px;top:2273px;width:301px;height:286px;background:linear-gradient(180deg,#7b93ad,#5a4a3a 55%,#4a5a3a)"></div>
  <div class="abs tile tile-gold" style="left:111px;top:2585px;width:300px;height:286px">
    <div class="inner">
      <svg width="34" height="42" viewBox="0 0 34 42" fill="none" stroke="#3a2a0c" stroke-width="2.5"><path d="M17 40 C6 26 3 21 3 15 A14 14 0 0 1 31 15 C31 21 28 26 17 40Z"/><circle cx="17" cy="15" r="5"/></svg>
      <span>Lorem Ipsum is simply dummy text of the printing</span>
    </div>
  </div>
  <div class="abs tile" role="img" aria-label="Modern stone and timber home with paved driveway" style="left:432px;top:2585px;width:651px;height:286px;background:linear-gradient(180deg,#c6cbcf,#bfae96 55%,#9d8f7a)"></div>
  <a class="abs btn btn-gold view-more">View More</a>
</section>

<section class="location">
  <div class="abs" role="img" aria-label="Street map of western Sydney suburbs with location pins" style="left:0;top:0;width:640px;height:565px;background:linear-gradient(90deg,#e0e2da,#d2d4c8 70%,rgba(138,106,44,0))"></div>
  <h2>Location We Serve</h2>
  <div class="abs loc-search">Search<span class="go"><svg width="22" height="22" viewBox="0 0 22 22" fill="none" stroke="#fff" stroke-width="2"><circle cx="9" cy="9" r="7"/><path d="M14 14 L20 20"/></svg></span></div>
  <ul class="abs loc-list">
    <li><svg width="14" height="18" viewBox="0 0 14 18" fill="#fff"><path d="M7 18 C2 11 1 9 1 6.5 A6 6 0 0 1 13 6.5 C13 9 12 11 7 18Z M7 4 A2.5 2.5 0 1 0 7 9 A2.5 2.5 0 1 0 7 4Z"/></svg>Lorem Ipsum</li>
    <li><svg width="14" height="18" viewBox="0 0 14 18" fill="#fff"><path d="M7 18 C2 11 1 9 1 6.5 A6 6 0 0 1 13 6.5 C13 9 12 11 7 18Z M7 4 A2.5 2.5 0 1 0 7 9 A2.5 2.5 0 1 0 7 4Z"/></svg>Lorem Ipsum</li>
    <li><svg width="14" height="18" viewBox="0 0 14 18" fill="#fff"><path d="M7 18 C2 11 1 9 1 6.5 A6 6 0 0 1 13 6.5 C13 9 12 11 7 18Z M7 4 A2.5 2.5 0 1 0 7 9 A2.5 2.5 0 1 0 7 4Z"/></svg>Lorem Ipsum</li>
    <li><svg width="14" height="18" viewBox="0 0 14 18" fill="#fff"><path d="M7 18 C2 11 1 9 1 6.5 A6 6 0 0 1 13 6.5 C13 9 12 11 7 18Z M7 4 A2.5 2.5 0 1 0 7 9 A2.5 2.5 0 1 0 7 4Z"/></svg>Lorem Ipsum</li>
    <li><svg width="14" height="18" viewBox="0 0 14 18" fill="#fff"><path d="M7 18 C2 11 1 9 1 6.5 A6 6 0 0 1 13 6.5 C13 9 12 11 7 18Z M7 4 A2.5 2.5 0 1 0 7 9 A2.5 2.5 0 1 0 7 4Z"/></svg>Lorem Ipsum</li>
    <li><svg width="14" height="18" viewBox="0 0 14 18" fill="#fff"><path d="M7 18 C2 11 1 9 1 6.5 A6 6 0 0 1 13 6.5 C13 9 12 11 7 18Z M7 4 A2.5 2.5 0 1 0 7 9 A2.5 2.5 0 1 0 7 4Z"/></svg>Lorem Ipsum</li>
    <li><svg width="14" height="18" viewBox="0 0 14 18" fill="#fff"><path d="M7 18 C2 11 1 9 1 6.5 A6 6 0 0 1 13 6.5 C13 9 12 11 7 18Z M7 4 A2.5 2.5 0 1 0 7 9 A2.5 2.5 0 1 0 7 4Z"/></svg>Lorem Ipsum</li>
    <li><svg width="14" height="18" viewBox="0 0 14 18" fill="#fff"><path d="M7 18 C2 11 1 9 1 6.5 A6 6 0 0 1 13 6.5 C13 9 12 11 7 18Z M7 4 A2.5 2.5 0 1 0 7 9 A2.5 2.5 0 1 0 7 4Z"/></svg>Lorem Ipsum</li>
  </ul>
</section>

<section class="contact-bg" role="img" aria-label="Aerial view of suburban rooftops at dusk"></section>

<section style="top:0;height:0">
  <h2 class="abs section-title" style="top:3712px">Contact Us</h2>
  <div class="abs contact-card">
    <h3>Contact With Us</h3>
    <div class="field" style="left:34px;top:92px;width:247px">First Name</div>
    <div class="field" style="left:324px;top:92px;width:247px">Last Name</div>
    <div class="field" style="left:34px;top:182px;width:247px">Email Address</div>
    <div class="field" style="left:324px;top:182px;width:247px">Phone Number</div>
    <div class="field" style="left:34px;top:260px;width:560px;height:90px">Message</div>
    <a class="abs btn btn-gold submit">Submit Now</a>
    <div class="abs address">
      <h3 class="abs">Address</h3>
      <div class="addr-row" style="top:80px">
        <span class="ico"><svg width="22" height="26" viewBox="0 0 22 26" fill="none" stroke="#fff" stroke-width="1.8"><path d="M11 25 C4 16 2 13 2 10 A9 9 0 0 1 20 10 C20 13 18 16 11 25Z"/><circle cx="11" cy="10" r="3"/></svg></span>
        <span>Shop 2217B<br>Level 1 Harbourgate<br>Shopping Centre<br>87 Quillon Terrace<br>Southport</span>
      </div>
      <div class="addr-row" style="top:250px;align-items:center">
        <span class="ico"><svg width="24" height="24" viewBox="0 0 24 24" fill="none" stroke="#fff" stroke-width="1.8"><path d="M5 2 L9 2 L11 7 L8 9 C9.5 12 12 14.5 15 16 L17 13 L22 15 L22 19 C22 21 20 22 18 22 C9 21 3 15 2 6 C2 4 3 2 5 2Z"/></svg></span>
        <span>+1800 555 0142</span>
      </div>
      <div class="addr-row" style="top:336px;align-items:center">
        <span class="ico"><svg width="24" height="18" viewBox="0 0 24 18" fill="none" stroke="#fff" stroke-width="1.8"><rect x="1" y="1" width="22" height="16"/><path d="M1 1 L12 10 L23 1"/></svg></span>
        <span>info@agentpivola.com</span>
      </div>
    </div>
  </div>
</section>

<footer style="top:0;height:0">
  <div class="abs footer-name">AGENT PIVOLA</div>
  <nav class="abs footer-nav"><a>Home</a><a>Buy</a><a>Sell</a><a>Sold</a><a>Lease</a><a>Agents</a><a>Concierge</a></nav>
  <div class="abs footer-rule"></div>
  <p class="abs copy">© 2025 Agent Pivola | All Rights Reserved | Privacy Policy</p>
</footer>

</body>
</html>
```